Website Design Needed for Performance Horse Trading Business

We require a website designed for Saddlewend, a new business which lists top quality performance stock horse bloodlines for sale. Our Australian company caters to the Australian Stock Horse, Quarter Horse and Paint Horse breeds of horse used for performance events such as Camp drafting and Cutting. The website design needs to communicate quality, have a professional look while maintaining a western, rural feel.
Colour schemes that we are looking for are either grey and orange, navy and grey or brown and grey.
The logo for the website has been attached below
Design deliverables are as follows:
-Main Page
-Horses for Sale Page
-Horse Listing Page
-Html & CSS files for pages
MAIN PAGE
----------------
Description: This page is where customers land, search for horses, see premium horses
Elements which need to be included on the main page are
-a horse filter section, allowing customers to search for horse listings by filtering attributes.
-premium listings displaying large photos of horse, price and location.
Horses for Sale PAGE
---------------------------------
Description: This page displays a list of available horses for sale as per the filtered results.
Elements which need to be included on this page are
- a filter panel which allows customers to filter results
- list of horses available for sale
Horse Listing Page
-------------------------------
Description: This page displays all the information about the horse for sale.
Screenshots of the basic program are attached for the Horses for Sale Page and the Horse Listing Page to give an idea of the elements required ONLY and should not be thought of as a design guideline.
Webpage HEADER
-------------------------
The Header section of the website should include login/signup buttons, 'my account' buttons (or links) as well as a featured link/button that says 'Sell Your Horse'
Updates
Thank you all for your designs so far. We would like to see the Sell Your Horse section featured more in the website design to attract customers. This would be as a button or highlighted link that is eye catching in the primary section of the website design of the main page. Perhaps placing it on the right hand side adjacent to the search function lets customers make the mental decision as to whether they are looking to buy or looking to sell when they visit the website. The wording above or near the button would be 'Advertise your horse with us' with the words on the button being 'Create Ad!'.
Industry/Entity Type
Events
Look and feel
Each slider illustrates characteristics of the customer's brand and the style your logo design should communicate.

```html
<!DOCTYPE html>
<html lang="en">
<head>
<meta charset="utf-8">
<title>Saddlewend – Performance Stock Horses</title>
<link rel="stylesheet" href="https://fonts.googleapis.com/css2?family=Open+Sans:wght@400;600;700&family=Poiret+One&family=Roboto:wght@400;500&display=swap">
<style>
:root{
  --orange:#e28a1c;
  --orange-dark:#c8750f;
  --charcoal:#3b3b3b;
  --charcoal-deep:#2e2e2e;
  --ink:#333;
  --muted:#555;
  --line:#e2e2e2;
  --white:#fff;
  --slate:#5e7a86;
}
*{box-sizing:border-box;margin:0;padding:0}
html,body{width:686px;height:1200px;overflow:hidden;background:var(--white)}
body{font-family:"Open Sans",Arial,sans-serif;color:var(--ink);position:relative}
.abs{position:absolute}

/* header */
.site-header{position:absolute;left:0;top:0;width:686px;height:63px;background:var(--white)}
.brand{left:56px;top:14px;display:flex;align-items:center;gap:8px}
.brand-mark{width:12px;height:12px;background:var(--charcoal);border-radius:50%}
.brand-name{font-family:"Open Sans",sans-serif;font-weight:700;font-size:22px;color:var(--charcoal-deep);letter-spacing:.5px}
.brand-sub{left:78px;top:42px;font-size:5px;letter-spacing:10px;color:var(--charcoal)}
.account-links{right:57px;top:13px;font-size:8px;color:var(--muted);display:flex;gap:18px}
.btn-head{top:35px;height:17px;font-size:8.5px;font-weight:600;color:var(--white);display:flex;align-items:center;justify-content:center}
.btn-signup{left:507px;width:58px;background:var(--charcoal)}
.btn-login{left:570px;width:59px;background:var(--orange)}

/* nav */
.main-nav{top:63px;left:0;width:686px;height:28px;background:var(--charcoal)}
.main-nav a{position:absolute;top:0;height:28px;line-height:28px;text-align:center;color:var(--white);font-size:8px;font-weight:600;text-decoration:none;border-right:1px solid #4a4a4a}
.main-nav a.active{background:var(--orange)}

/* hero */
.hero{top:91px;left:0;width:686px;height:333px;background:linear-gradient(100deg,#c9a66c 0%,#e8d8b2 30%,#b79270 55%,#6a4a36 72%,#cdb68a 100%)}
.hero-arrow{left:13px;top:242px}
.hero-card{left:54px;top:196px;width:308px;height:142px;background:rgba(255,255,255,.85);text-align:center}
.hero-title{font-family:"Poiret One",cursive;font-size:21px;color:#222;margin-top:20px;font-weight:400}
.hero-text{font-family:"Roboto",sans-serif;font-size:7.6px;line-height:12.5px;color:#333;margin:8px 20px 0}
.hero-actions{left:52px;top:99px;width:198px;height:29px;display:flex}
.hero-actions span{display:flex;align-items:center;justify-content:center;font-family:"Roboto",sans-serif;font-size:9.5px;color:var(--white)}
.hero-read{width:100px;background:var(--orange)}
.hero-gallery{width:98px;background:var(--charcoal)}
.hero-or{left:90px;top:5px;width:19px;height:19px;border-radius:50%;background:var(--white);color:#222;font-size:7.5px;font-style:italic;font-weight:700;display:flex;align-items:center;justify-content:center}

/* search */
.search-band{top:424px;left:0;width:686px;height:57px;background:var(--orange)}
.search-title{left:57px;top:17px;color:var(--white);font-size:16.5px;letter-spacing:.3px}
.field{top:18px;height:21px;background:var(--white);font-size:8.5px;color:#444;padding-left:7px;line-height:21px}
.field-category{left:186px;width:142px}
.field-caret{right:0;top:0;width:21px;height:21px;background:var(--charcoal)}
.field-keyword{left:334px;width:143px}
.search-btn{left:486px;top:18px;width:143px;height:21px;background:var(--charcoal);color:var(--white);font-size:8.5px;text-align:center;line-height:21px}

/* about */
.section-title{left:0;width:686px;text-align:center;font-size:13.5px;color:#222;letter-spacing:.2px}
.about-text{left:58px;top:522px;width:570px;text-align:center;font-size:7.6px;line-height:11px;color:var(--muted)}
.small-btn{background:var(--orange);color:var(--white);font-size:7.5px;text-align:center;border-bottom:2px solid var(--orange-dark)}

/* listings */
.listing{top:662px;width:132px;height:228px;background:var(--white);box-shadow:0 1px 3px rgba(0,0,0,.28)}
.listing-photo{width:132px;height:168px}
.listing-name{text-align:center;font-size:9.6px;color:#555;margin-top:7px}
.listing-price{text-align:center;font-size:10px;color:var(--orange);margin-top:3px}
.listing-loc{text-align:center;font-size:6.4px;color:#444;margin-top:4px}
.view-badge{left:50px;top:66px;width:38px;height:38px;border-radius:50%;background:var(--white)}

/* blog */
.post-photo{width:80px;height:83px}
.post-title{font-size:8px;font-weight:600;color:#222;line-height:10.5px}
.post-text{font-size:6.6px;color:#555;line-height:8.2px}
.tags{display:flex;gap:4px}
.tag{height:11px;font-size:5px;font-weight:700;color:var(--white);display:flex;align-items:center;justify-content:center}
.tag-date{width:43px;background:var(--orange)}
.tag-count{width:20px;background:var(--slate)}
.tag-more{width:41px;background:var(--charcoal)}

/* footer */
.site-footer{top:1109px;left:0;width:686px;height:91px;background:var(--charcoal)}
.footer-links{top:23px;left:0;width:686px;text-align:center;font-size:8px;color:var(--white)}
.footer-links span.sep{margin:0 6px}
.copyright{top:41px;left:0;width:686px;text-align:center;font-size:7px;color:var(--white)}
.social{top:59px;left:310px;display:flex;gap:3px}
.social i{display:block;width:19px;height:19px;border-radius:50%;background:var(--orange)}
</style>
</head>
<body>

<header class="site-header">
  <div class="abs brand"><span class="brand-mark"></span><span class="brand-name">SADDLEWEND</span></div>
  <div class="abs brand-sub">AUSTRALIA</div>
  <div class="abs account-links"><span>My Account</span><span>|</span><span>Sell Your Horse</span></div>
  <div class="abs btn-head btn-signup">Signup</div>
  <div class="abs btn-head btn-login">Login</div>
</header>

<nav class="abs main-nav">
  <a class="active" style="left:58px;width:94px">Home</a>
  <a style="left:152px;width:95px">About Us</a>
  <a style="left:247px;width:74px">Service</a>
  <a style="left:321px;width:116px">Premium Listings</a>
  <a style="left:437px;width:73px">Gallery</a>
  <a style="left:510px;width:92px;border-right:none">Contact Us</a>
</nav>

<section class="abs hero" role="img" aria-label="Close-up photo of a brown and white paint horse in a sunlit field">
  <svg class="abs hero-arrow" width="22" height="22" viewBox="0 0 22 22"><circle cx="11" cy="11" r="10" fill="none" stroke="#fff" stroke-opacity=".7" stroke-width="1.5"/><path d="M15 11H7M10 7.5 6.5 11 10 14.5" fill="none" stroke="#fff" stroke-opacity=".8" stroke-width="1.5"/></svg>
</section>
<div class="abs hero-card">
  <h1 class="hero-title">Saddlewend</h1>
  <p class="hero-text">Curabitur lobortis libero a rutrum tristique. Cras ipsum mauris, porttitor eu pulvinar sit amet, sollicitudin nec lectus. Sed lorem justo, ullamcorper malesuada porta non, vehicula sed lacus.</p>
  <div class="abs hero-actions">
    <span class="hero-read">Read More</span><span class="hero-gallery">VIEW GALLERY</span>
    <span class="abs hero-or">or</span>
  </div>
</div>

<section class="abs search-band">
  <div class="abs search-title">Search Horse</div>
  <div class="abs field field-category">Category
    <svg class="abs field-caret" viewBox="0 0 21 21"><rect width="21" height="21" fill="#3b3b3b"/><path d="M6.5 8.5h8l-4 4.5z" fill="#fff"/></svg>
  </div>
  <div class="abs field field-keyword">Keyword</div>
  <div class="abs search-btn">Search Now</div>
</section>

<h2 class="abs section-title" style="top:497px;font-weight:400">ABOUT US</h2>
<p class="abs about-text">Our company caters to the Australian Stock Horse, Quarter Horse and Paint Horse breeds of horse used for performance events such as Camp drafting and Cutting.Sed non sollicitudin dui. Aenean commodo odio nisl, scelerisque volutpat est ornare in. Sed placerat rhoncus laoreet. Aenean laoreet elit arcu, ut dignissim leo fermentum id. Etiam justo neque, semper a pretium vel, malesuada ac ex. Curabitur vel neque consectetur, imperdiet tortor eget, convallis ligula. Proin ornare urna ligula, ut placerat massa tempus vitae. Nunc accumsan placerat libero,</p>
<div class="abs small-btn" style="left:307px;top:582px;width:71px;height:15px;line-height:13px">Read More</div>

<svg class="abs" style="left:56px;top:628px" width="15" height="15" viewBox="0 0 15 15"><circle cx="7.5" cy="7.5" r="6.5" fill="none" stroke="#999" stroke-width="1.2"/><path d="M10.5 7.5h-6M7 5 4.5 7.5 7 10" fill="none" stroke="#999" stroke-width="1.2"/></svg>
<h2 class="abs section-title" style="top:629px;font-weight:400">OUR PREMIUM LISTINGS</h2>
<svg class="abs" style="left:616px;top:628px" width="15" height="15" viewBox="0 0 15 15"><circle cx="7.5" cy="7.5" r="6.5" fill="none" stroke="#e28a1c" stroke-width="1.2"/><path d="M4.5 7.5h6M8 5l2.5 2.5L8 10" fill="none" stroke="#e28a1c" stroke-width="1.2"/></svg>

<article class="abs listing" style="left:58px">
  <div class="listing-photo" role="img" aria-label="Horse galloping at sunset" style="background:linear-gradient(180deg,#e0a25a,#c8843e 60%,#b87a3e)"></div>
  <svg class="abs view-badge" viewBox="0 0 38 38"><circle cx="19" cy="19" r="19" fill="#fff"/><path d="M10 19c4-6 14-6 18 0-4 6-14 6-18 0z" fill="#111"/><circle cx="19" cy="19" r="3" fill="#fff"/><circle cx="19" cy="19" r="1.6" fill="#111"/></svg>
  <div class="listing-name">Lorem ipsum Dolor</div>
  <div class="listing-price">$3892.29</div>
  <div class="listing-loc">Contantry popilar sit</div>
</article>
<article class="abs listing" style="left:205px">
  <div class="listing-photo" role="img" aria-label="Bay horse trotting in a sandy yard" style="background:linear-gradient(180deg,#9eaa8c,#b89a78 50%,#c49a74)"></div>
  <div class="listing-name">Lorem ipsum Dolor</div>
  <div class="listing-price">$3892.29</div>
  <div class="listing-loc">Contantry popilar sit</div>
</article>
<article class="abs listing" style="left:351px">
  <div class="listing-photo" role="img" aria-label="Bay horse head wearing a bridle" style="background:linear-gradient(120deg,#3a2018,#7a3820 45%,#e6e4c0 75%)"></div>
  <div class="listing-name">Lorem ipsum Dolor</div>
  <div class="listing-price">$3892.29</div>
  <div class="listing-loc">Contantry popilar sit</div>
</article>
<article class="abs listing" style="left:498px">
  <div class="listing-photo" role="img" aria-label="Dun horse running across a pale plain" style="background:linear-gradient(180deg,#d8d2c8,#c4b8a6 55%,#bfb09a)"></div>
  <div class="listing-name">Lorem ipsum Dolor</div>
  <div class="listing-price">$3892.29</div>
  <div class="listing-loc">Contantry popilar sit</div>
</article>

<svg class="abs" style="left:56px;top:926px" width="15" height="15" viewBox="0 0 15 15"><circle cx="7.5" cy="7.5" r="6.5" fill="none" stroke="#999" stroke-width="1.2"/><path d="M10.5 7.5h-6M7 5 4.5 7.5 7 10" fill="none" stroke="#999" stroke-width="1.2"/></svg>
<h2 class="abs section-title" style="top:926px;font-weight:400">LATEST BLOG</h2>
<svg class="abs" style="left:616px;top:926px" width="15" height="15" viewBox="0 0 15 15"><circle cx="7.5" cy="7.5" r="6.5" fill="none" stroke="#e28a1c" stroke-width="1.2"/><path d="M4.5 7.5h6M8 5l2.5 2.5L8 10" fill="none" stroke="#e28a1c" stroke-width="1.2"/></svg>

<article>
  <div class="abs post-photo" style="left:58px;top:967px;background:linear-gradient(180deg,#8a4a2c,#c07040 55%,#6a7a2a)" role="img" aria-label="Dark horse running through a meadow at dusk"></div>
  <h3 class="abs post-title" style="left:150px;top:967px;width:180px">Brookvale Trading Group Participating in the 2014 Ridgeline Golf Tournament</h3>
  <p class="abs post-text" style="left:150px;top:995px;width:175px">mollis varius dolor id, varius molestie urna. Cras id tellus nisl. Fusce purus ante, elementum id metus eget, congue pharetra dolor. Sed non mollis quam. Nulla non eros diam.</p>
  <div class="abs tags" style="left:150px;top:1039px"><span class="tag tag-date">05 june 15</span><span class="tag tag-count">12</span><span class="tag tag-more">Read More</span></div>
</article>
<article>
  <div class="abs post-photo" style="left:362px;top:967px;background:linear-gradient(90deg,#1a1a1a,#6a6a66 40%,#2a2a2a)" role="img" aria-label="White and dark horses standing side by side"></div>
  <h3 class="abs post-title" style="left:453px;top:967px;width:180px">New Product: Foreign Exchange</h3>
  <p class="abs post-text" style="left:453px;top:984px;width:178px">mollis varius dolor id, varius molestie urna. Cras id tellus nisl. Fusce purus ante, elementum id metus eget, congue pharetra dolor. Sed non mollis quam. Nulla non eros diam. Proin ultricies, felis eget sceler-isque</p>
  <div class="abs tags" style="left:453px;top:1039px"><span class="tag tag-date">05 june 15</span><span class="tag tag-count">12</span><span class="tag tag-more">Read More</span></div>
</article>

<footer class="abs site-footer">
  <div class="abs footer-links">Home<span class="sep">|</span>About Us<span class="sep">|</span>Service<span class="sep">|</span>Premium Listings<span class="sep">|</span>Gallery<span class="sep">|</span>Contact Us</div>
  <div class="abs copyright">Copyright(c) website name. Allrights Reserved</div>
  <div class="abs social" aria-label="Social links"><i></i><i></i><i></i></div>
</footer>

</body>
</html>
```